Guided Study Tour - Klangtage Wendorf Two Sided Flyer

We need a two-sided flyer for a Guided Study Tour to Klangtage Wendorf. We want beautiful pictures of Germany and if possible some of the Halbig venues our participants will be visiting. I have also provided the content that needs to be included. Also, in the attached document I provided a link to the Klangtage event. Please read and watch the video to be inspired.
This flyer should be beautiful and engaging. It needs to grab your attention right away and really highlight the wonderful things that they will be doing and that are included in the tour. This is a once in a lifetime opportunity for people to experience. We are targeting Music Directors and Music professionals.
Both attached logos need to be present on the flyer.

```html
<!DOCTYPE html>
<html lang="en">
<head>
<meta charset="utf-8">
<title>Guided Study Tour – Klangtage Wendorf</title>
<link href="https://fonts.googleapis.com/css2?family=Zilla+Slab:ital,wght@0,400;0,600;1,400&family=Roboto+Slab:wght@300&family=Allura&display=swap" rel="stylesheet">
<style>
  :root {
    --panel: #2b3034;
    --panel-dark: #24282b;
    --ink: #1d1d1d;
    --light: #e4e4e2;
    --white: #ffffff;
    --lime: #c8e62e;
    --sky-top: #b9c3d3;
    --sky-mid: #dfe3ea;
    --roof: #9a5e48;
    --lawn: #5f9a2f;
  }
  * { margin: 0; padding: 0; box-sizing: border-box; }
  html, body { width: 800px; height: 1200px; overflow: hidden; background: var(--panel); }
  .flyer { position: relative; width: 800px; height: 1200px; overflow: hidden;
    background: radial-gradient(ellipse at 50% 40%, var(--panel) 0%, var(--panel-dark) 100%); }

  .hero-photo { position: absolute; left: 0; top: 0; width: 800px; height: 570px;
    background: linear-gradient(180deg, var(--sky-top) 0%, var(--sky-mid) 28%, #c9cfd6 38%,
      #8f8a84 46%, var(--roof) 58%, #8c8a80 72%, #6f8a5a 84%, var(--lawn) 100%); }

  .event-header { position: absolute; left: 68px; top: 45px; height: 150px;
    border-left: 1.5px solid var(--ink); padding-left: 17px; color: var(--ink);
    font-family: "Zilla Slab", serif; }
  .event-date { font-size: 26px; font-weight: 400; line-height: 30px; letter-spacing: 0.3px; }
  .event-title { font-size: 25px; font-weight: 600; line-height: 34px; }
  .event-place { font-size: 25px; font-style: italic; line-height: 32px; }
  .event-extra { font-size: 18px; line-height: 23px; margin-top: 2px; }

  .invite { position: absolute; left: 44px; top: 470px; color: var(--white);
    font-family: "Allura", cursive; font-size: 40px; }
  .leader { position: absolute; left: 45px; top: 527px; color: var(--white);
    font-family: "Zilla Slab", serif; font-size: 14px; }

  .highlights { position: absolute; top: 610px; font-family: "Roboto Slab", serif;
    font-weight: 300; color: var(--light); }
  .highlights h2 { font-family: "Zilla Slab", serif; font-weight: 400; font-size: 19px;
    letter-spacing: 0.4px; margin-bottom: 10px; color: var(--white); }
  .highlights ul { list-style: none; }
  .highlights li { position: relative; padding-left: 10px; font-size: 17.5px;
    line-height: 21px; margin-bottom: 9px; }
  .highlights li::before { content: "•"; position: absolute; left: 0; font-size: 12px; }
  .festival { left: 50px; width: 350px; }
  .tour { left: 476px; width: 290px; }
  .column-divider { position: absolute; left: 436px; top: 616px; width: 1px; height: 362px;
    background: var(--light); }

  .testimonial { position: absolute; left: 55px; top: 1028px; width: 700px;
    font-family: "Allura", cursive; color: var(--lime); font-size: 27px; line-height: 36px; }
  .testimonial .second { display: block; padding-left: 82px; }
  .attribution { position: absolute; left: 240px; top: 1112px; font-family: "Roboto Slab", serif;
    font-weight: 300; color: var(--light); font-size: 17px; line-height: 21px; }
  .attribution .role { display: block; padding-left: 165px; }
</style>
</head>
<body>
<div class="flyer">
  <div class="hero-photo" role="img" aria-label="Aerial photograph of Wendorf city centre with red roofs, office blocks, a church spire and a green lawn under a cloudy sky"></div>

  <header class="event-header">
    <p class="event-date">JUNE 12 - 16, 2019</p>
    <h1 class="event-title">Guided Study Tour – Klangtage</h1>
    <p class="event-place">Wendorf, Germany</p>
    <p class="event-extra">Plus day trip to Dresden and full day<br>and overnight in Prague</p>
  </header>

  <p class="invite">Join us for a once in a lifetime</p>
  <p class="leader">.....led by Daniel Marsh........</p>

  <section class="highlights festival">
    <h2>KLANGTAGE HIGHLIGHTS:</h2>
    <ul>
      <li>More than 100 Concerts in 42 different Halbig venues</li>
      <li>World Class Musicians &amp; Celebrated Recording Artists</li>
      <li>Day trips to Weimer &amp; Dresden</li>
      <li>Bilingual pre-concert talks &amp; lectures with Halbig Scholars</li>
      <li>Featured Performers:</li>
      <li>Marco Verell, Pieter Lindaal, Cantorum Nova, Wendorf</li>
      <li>Hallenhof Orchestra, Vielle Quintet,&amp; the Wendorf Knabenchor</li>
    </ul>
  </section>

  <div class="column-divider"></div>

  <section class="highlights tour">
    <h2>STUDY TOUR HIGHLIGHTS:</h2>
    <ul>
      <li>Access to dress rehearsals</li>
      <li>Meet the artist opportunities</li>
      <li>Post-concert discussions led by Daniel Marsh</li>
      <li>Study sessions on Halbig’s B-Minor Mass, Magnificat,</li>
      <li>St. John Passion, St. Matthew Passion &amp; Weimar Cantatashours</li>
      <li>Guidance in planning individual concert itinerary</li>
      <li>Professional development or continuing education credit</li>
    </ul>
  </section>

  <blockquote class="testimonial">
    “This is where it all has begun...this is why our guests have tears in
    <span class="second">their eyes listening to the St. Matthew Passion or the B-Minor Mass.”</span>
  </blockquote>
  <p class="attribution">~ Stefan Krall, Musicologist,<span class="role">Festival Director</span></p>
</div>
</body>
</html>
```